Business card design for my company.
I would like the card's background colour to be black. You can also see our web site to get an idea of our brand. https://www.tmwhomecrafting.com.au/
- Name
- Email

```html
<!DOCTYPE html>
<html lang="en">
<head>
<meta charset="utf-8">
<title>TMW Home Crafting – Business Card</title>
<link href="https://fonts.googleapis.com/css2?family=Heebo:wght@400;500;700&display=swap" rel="stylesheet">
<style>
  :root {
    --page-bg: #f3f3f3;
    --card-bg: #222226;
    --brand-green: #189b4a;
    --text-light: #f4f5f7;
    --mark-dark: #0c0c0e;
  }
  * { margin: 0; padding: 0; box-sizing: border-box; }
  html, body {
    width: 1200px; height: 987px; overflow: hidden;
    background: var(--page-bg);
    font-family: "Heebo", Arial, sans-serif;
  }
  .card {
    position: absolute; left: 245px; width: 710px; height: 406px;
    background: var(--card-bg);
  }
  .card--front { top: 68px; }
  .card--back { top: 514px; }
  .edge-bar {
    position: absolute; top: 102px; width: 16px; height: 203px;
    background: var(--brand-green);
  }
  .edge-bar--left { left: 0; }
  .edge-bar--right { right: 0; }
  .highlight { color: var(--brand-green); }

  /* front */
  .front-name {
    position: absolute; left: 0; right: 0; top: 150px;
    text-align: center; font-size: 44px; font-weight: 700;
    color: var(--mark-dark); letter-spacing: 1px;
  }
  .front-web {
    position: absolute; left: 0; right: 0; top: 355px;
    text-align: center; font-size: 18px; color: var(--text-light);
    letter-spacing: 0.6px;
  }

  /* back */
  .back-name {
    position: absolute; left: 40px; width: 280px; top: 170px;
    text-align: center; font-size: 32px; font-weight: 700;
    line-height: 1.15; color: var(--text-light);
  }
  .divider {
    position: absolute; left: 354px; top: 97px; width: 1px; height: 211px;
    background: var(--brand-green);
  }
  .person {
    position: absolute; left: 395px; top: 130px;
  }
  .person__name {
    font-size: 31px; line-height: 34px; font-weight: 400;
    color: var(--text-light); letter-spacing: 0.5px;
  }
  .person__name strong { font-weight: 500; color: var(--brand-green); }
  .person__role {
    font-size: 16px; color: var(--text-light); letter-spacing: 0.6px;
  }
  .contact-list {
    position: absolute; left: 395px; top: 208px; list-style: none;
  }
  .contact-list li {
    display: flex; align-items: center; height: 22px;
    font-size: 16.5px; color: var(--text-light); letter-spacing: 0.6px;
  }
  .contact-list svg { width: 15px; height: 15px; margin-right: 9px; }
  .location {
    position: absolute; left: 0; right: 0; top: 349px;
    text-align: center; font-size: 16.5px; color: var(--brand-green);
    letter-spacing: 0.6px;
  }
</style>
</head>
<body>

<section class="card card--front">
  <div class="edge-bar edge-bar--left"></div>
  <div class="edge-bar edge-bar--right"></div>
  <div class="front-name">TMW Home Crafting</div>
  <div class="front-web">www.<span class="highlight">tmwhomecrafting</span>.com.au</div>
</section>

<section class="card card--back">
  <div class="edge-bar edge-bar--left"></div>
  <div class="edge-bar edge-bar--right"></div>
  <div class="back-name">TMW<br>Home Crafting</div>
  <div class="divider"></div>
  <div class="person">
    <div class="person__name"><strong>Liam</strong> Hartley</div>
    <div class="person__role">General Manager</div>
  </div>
  <ul class="contact-list">
    <li>
      <svg viewBox="0 0 16 16" aria-hidden="true"><path fill="#189b4a" d="M3.6 1.5l2.2 2.6-1.3 1.6c.9 2 2.6 3.7 4.6 4.6l1.6-1.3 2.6 2.2-1.2 2.2C7.3 13.2 2.8 8.7 1.4 2.7z"/></svg>
      0400 123 456
    </li>
    <li>
      <svg viewBox="0 0 16 16" aria-hidden="true"><circle cx="8" cy="8" r="6.5" fill="none" stroke="#189b4a" stroke-width="1.6"/><path fill="none" stroke="#189b4a" stroke-width="1.2" d="M1.5 8h13M8 1.5c-2.5 3-2.5 10 0 13M8 1.5c2.5 3 2.5 10 0 13"/></svg>
      www.<span class="highlight">tmwhomecrafting</span>.com.au
    </li>
    <li>
      <svg viewBox="0 0 16 16" aria-hidden="true"><rect x="1.5" y="4" width="13" height="9" fill="none" stroke="#189b4a" stroke-width="1.5"/><path fill="none" stroke="#189b4a" stroke-width="1.4" d="M1.5 4l6.5 5 6.5-5"/></svg>
      info@<span class="highlight">tmwhomecrafting</span>.com.au
    </li>
  </ul>
  <div class="location">Ballarat, Victoria, Australia</div>
</section>

</body>
</html>
```